Falbrook Company Notepad / Grid pad / Graph pad

I need a "modern" version of this graph pad. The information at the top needs to be shown, along with the graph lines, however, I need this more "interesting" than it currently is. This will be printed and bound at the TOP edge with 50 sheets per pack.

Target Market(s)

Clients - Want to show sophistication and not childish.

Industry/Entity Type

Structural Engineering

Font styles to use
Sans Serif

Colors
0255a3
85abd2

Requirements
Must have
• My project must have all of the elements currently shown on the pdf
Should not have
• My project should not have clipart images.

Files

```html
<!DOCTYPE html>
<html lang="en">
<head>
<meta charset="utf-8">
<title>Falbrook Company Graph Pad</title>
<link rel="stylesheet" href="https://fonts.googleapis.com/css2?family=Source+Sans+3:wght@400;600;700&display=swap">
<style>
  :root {
    --backdrop: #acaaab;
    --paper: #f5f4f2;
    --brand-blue: #21527a;
    --brand-green: #00b05a;
    --field: #e4e3e3;
    --grid-line: #cbcbcb;
    --grid-frame: #7a7a7a;
    --ink: #1f1f1f;
    --muted: #8a8a8a;
  }
  * { box-sizing: border-box; margin: 0; padding: 0; }
  html, body { width: 956px; height: 1200px; overflow: hidden; }
  body {
    background: var(--backdrop);
    font-family: "Source Sans 3", Arial, sans-serif;
    position: relative;
  }
  .sheet {
    position: absolute; left: 95px; top: 51px;
    width: 773px; height: 1092px;
    background: var(--paper);
    box-shadow: 0 2px 10px rgba(0,0,0,0.25);
  }
  .accent-bar {
    position: absolute; left: 0; top: 41px;
    width: 33px; height: 104px;
    background: var(--brand-green);
  }
  .brand {
    position: absolute; left: 50px; top: 70px;
    width: 220px; text-align: center;
  }
  .brand-name {
    font-size: 24px; font-weight: 700; letter-spacing: 0.5px;
    color: var(--brand-blue); line-height: 1.05;
  }
  .brand-tagline {
    margin-top: 6px; font-size: 8px; font-weight: 600;
    color: var(--muted); letter-spacing: 0.2px;
  }
  .info-panel {
    position: absolute; left: 286px; top: 41px;
    width: 487px; height: 104px;
    background: var(--brand-blue);
  }
  .field-label {
    position: absolute; color: #fff;
    font-size: 12.5px; font-weight: 600;
    line-height: 22px; text-align: right;
  }
  .field-box {
    position: absolute; height: 22px;
    background: var(--field);
  }
  .grid-area {
    position: absolute; left: 54px; top: 195px;
    width: 670px; height: 796px;
    border: 1px solid var(--grid-frame);
    background-image:
      linear-gradient(to right, var(--grid-line) 1px, transparent 1px),
      linear-gradient(to bottom, var(--grid-line) 1px, transparent 1px);
    background-size: 21px 21px;
    background-position: -1px -1px;
  }
  .contact-line {
    position: absolute; left: 66px; top: 1031px;
    display: flex; align-items: center;
    font-size: 13.5px; color: var(--ink); white-space: nowrap;
  }
  .contact-line svg { width: 11px; height: 11px; fill: var(--brand-blue); flex: none; }
  .contact-item { display: flex; align-items: center; gap: 8px; margin-right: 12px; }
</style>
</head>
<body>
  <div class="sheet">
    <div class="accent-bar"></div>

    <div class="brand">
      <div class="brand-name">FALBROOK<br>COMPANY</div>
      <div class="brand-tagline">Precision | Structure | Insight</div>
    </div>

    <div class="info-panel">
      <span class="field-label" style="left:0;width:68px;top:12px">PROJECT</span>
      <span class="field-box" style="left:77px;top:12px;width:144px"></span>
      <span class="field-label" style="left:0;width:68px;top:38px">Task</span>
      <span class="field-box" style="left:77px;top:38px;width:144px"></span>
      <span class="field-label" style="left:0;width:68px;top:65px">Page</span>
      <span class="field-box" style="left:77px;top:65px;width:59px"></span>
      <span class="field-label" style="left:143px;width:14px;top:66px;text-align:left">of</span>
      <span class="field-box" style="left:161px;top:65px;width:60px"></span>

      <span class="field-label" style="left:230px;width:57px;top:12px">Job No</span>
      <span class="field-box" style="left:294px;top:12px;width:144px"></span>
      <span class="field-label" style="left:230px;width:57px;top:38px">Author</span>
      <span class="field-box" style="left:294px;top:38px;width:144px"></span>
      <span class="field-label" style="left:230px;width:57px;top:65px">Date</span>
      <span class="field-box" style="left:294px;top:65px;width:144px"></span>
    </div>

    <div class="grid-area"></div>

    <div class="contact-line">
      <span class="contact-item">
        <svg viewBox="0 0 12 12"><path d="M6 0a4 4 0 0 0-4 4c0 3 4 8 4 8s4-5 4-8a4 4 0 0 0-4-4zm0 5.6A1.6 1.6 0 1 1 6 2.4a1.6 1.6 0 0 1 0 3.2z"/></svg>
        215 Harbor Lane, Suite 204, Lakeview, FL 33012
      </span>
      <span class="contact-item">
        <svg viewBox="0 0 12 12"><path d="M2.5 0.5l2 2.4-1 1.4c.7 1.6 2 2.9 3.6 3.6l1.4-1 2.4 2-1.2 2.3C5 11 1 7 .3 1.7z"/></svg>
        555.014.2290
      </span>
      <span class="contact-item">
        <svg viewBox="0 0 12 12"><circle cx="6" cy="6" r="5.5"/><path d="M3 3.5c1 0 1.5 1 1 2s.5 1.5 1.5 1.5-.5 2.5-1 3M8 2c-.5 1 .5 1.5 1 2s1 .5 1.5 0" stroke="#f5f4f2" stroke-width="1" fill="none"/></svg>
        www.falbrookcompany.com
      </span>
    </div>
  </div>
</body>
</html>
```